Dental Medical History Form - Content provided

Design a medical history form for a dental practice. Content is provided so all that is needed is the formatting to make it look great and easy to read.

"Patient Information" to include all information contained in top portion of the "Patient Medical History Form" docx file.

"Medical History" should follow the formatting and content of the "Exact Medical History" file as this is what the entry fields look like in our practice software and so we would like it to match.

1st page - Patient info, allergies, medications, antibiotics, joint replacement, pregnancy.

2nd page - Do you have, or have you had, any of the following? . . . . . . .
Updates

Target Market(s)

All ages but must be clear enough for elderly to read. Use as much space as possible to keep font size bigger yet keep to two pages

Industry/Entity Type

Dental

Font styles to use
Sans Serif

Requirements
Must have
• All content provided
• Our logo at the top (file provided)
• Century Gothic Font
• Limit to two pages

```html
<!DOCTYPE html>
<html lang="en">
<head>
<meta charset="utf-8">
<title>Crestline Dental – Confidential Medical History</title>
<link href="https://fonts.googleapis.com/css2?family=Open+Sans+Condensed:wght@300;700&family=Archivo+Black&display=swap" rel="stylesheet">
<style>
  :root{
    --bg:#e9e9e9;
    --paper:#fbfbfb;
    --ink:#3a3a3a;
    --soft:#6d6d6d;
    --rule:#c9c9c9;
    --box:#bdbdbd;
    --band-hi:#ffffff;
    --band-lo:#cfcfcf;
    --texture-a:#f7f7f7;
    --texture-b:#efefef;
  }
  *{box-sizing:border-box;margin:0;padding:0}
  html,body{width:1200px;height:784px;overflow:hidden;background:var(--bg)}
  body{font-family:"Open Sans Condensed",sans-serif;color:var(--ink)}
  .sheet{position:absolute;left:322px;top:12px;width:556px;height:760px;background:var(--paper);
    box-shadow:0 2px 8px rgba(0,0,0,.12);padding:18px 22px 16px;overflow:hidden}
  .sheet-texture{position:absolute;left:0;right:0;top:96px;bottom:0;
    background:linear-gradient(180deg,var(--texture-a),var(--texture-b));z-index:0}
  .content{position:relative;z-index:1}
  .masthead{display:flex;justify-content:space-between;align-items:flex-start;height:52px}
  .brand{display:flex;align-items:center;gap:6px;font-family:"Open Sans Condensed",sans-serif;font-weight:700;font-size:18px;color:var(--ink);line-height:1}
  .brand-mark{width:8px;height:8px;background:var(--ink)}
  .contact{text-align:right;font-weight:700;font-size:9px;line-height:1.3;color:var(--ink)}
  .contact .phone{font-size:12px}
  .title{font-family:"Archivo Black",sans-serif;font-size:13px;letter-spacing:4px;text-align:center;margin:-6px 0 12px}
  .row{display:flex;align-items:flex-end;gap:6px;height:19px;font-size:9px;white-space:nowrap}
  .label{font-weight:700}
  .field{flex:1;border-bottom:1px solid var(--rule);height:12px;position:relative}
  .field small{position:absolute;right:2px;top:-2px;font-size:7px;color:var(--soft)}
  .check{display:inline-block;width:9px;height:9px;border:1px solid var(--box);background:var(--paper);vertical-align:-1px;margin:0 3px}
  .band{height:16px;margin:8px -22px 6px;background:linear-gradient(var(--band-hi),var(--band-lo));
    display:flex;align-items:center;justify-content:center;font-weight:700;font-size:10px;
    box-shadow:inset 0 -1px 0 #bbb}
  .heading{font-weight:700;font-size:10px;text-align:center;margin:6px 0 3px}
  .options{display:flex;justify-content:space-between;font-size:9px;height:19px;align-items:center}
  .lines .field{flex:none;width:100%}
  .qa{display:flex;align-items:center;font-size:9px;height:26px;gap:4px}
  .qa .q{width:170px;font-weight:700}
  .turnover{position:absolute;left:0;bottom:16px;width:110px;height:18px;background:linear-gradient(var(--band-hi),var(--band-lo));
    font-weight:700;font-size:10px;display:flex;align-items:center;justify-content:center;box-shadow:inset 0 -1px 0 #bbb;z-index:1}
</style>
</head>
<body>
<main class="sheet">
  <div class="sheet-texture" role="img" aria-label="Faint light grey chevron background pattern"></div>
  <div class="content">
    <header class="masthead">
      <div class="brand"><span class="brand-mark"></span>Crestline Dental</div>
      <div class="contact"><div class="phone">(02) 40 555 010</div>Crestline Dental, Suite 4, 18 Harbour Rd<br>Bayview NSW 2104</div>
    </header>
    <h1 class="title">CONFIDENTIAL MEDICAL HISTORY</h1>

    <section class="patient">
      <div class="row"><span class="label">Name:</span><span class="field"><small>First</small></span><span class="field"><small>Middle</small></span><span class="field"><small>Last</small></span></div>
      <div class="row"><span class="label">Address:</span><span class="field"></span></div>
      <div class="row"><span class="label">DOB:</span><span class="field"></span><span class="label">Email Address:</span><span class="field"></span></div>
      <div class="row"><span class="label">Phone Number(s): Mobile</span><span class="field"></span><span class="label">Work</span><span class="field"></span><span class="label">Home</span><span class="field"></span></div>
      <div class="row"><span class="label">Emergency Contact Person: Name:</span><span class="field"></span><span class="label">Relationship:</span><span class="field"></span><span class="label">Phone number:</span><span class="field"></span></div>
    </section>

    <div class="band">General Practitioner:</div>
    <section class="practitioner">
      <div class="row"><span class="label">Name:</span><span class="field"></span><span class="label">Phone Number:</span><span class="field"></span></div>
      <div class="row"><span class="label">Practice Name:</span><span class="field"></span><span class="label">Referred by:</span><span class="field"></span></div>
      <div class="row"><span class="label">Do you have a health fund with dental cover?</span> Yes<span class="check"></span>or No<span class="check"></span><span class="label">If so, what is the name of the fund?</span><span class="field"></span></div>
      <div class="row"><span class="label">Fund Number:</span><span class="field"></span><span class="label">Priority Number on card:</span>0<span class="check"></span>1<span class="check"></span>2<span class="check"></span>3<span class="check"></span>4<span class="check"></span>5<span class="check"></span></div>
      <div class="row"><span class="label">Occupation:</span><span class="field"></span></div>
    </section>

    <div class="band"></div>
    <section class="allergies">
      <div class="options"><span>Aspirin<span class="check"></span></span><span>Codeine<span class="check"></span></span><span>Penicillin<span class="check"></span></span><span>Sulfites<span class="check"></span></span><span>Latex<span class="check"></span></span><span>Local Anaesthetic<span class="check"></span></span><span>Lactose<span class="check"></span></span><span>Nickel<span class="check"></span></span></div>
      <div class="row"><span class="label">Other:</span><span class="field"></span></div>
    </section>

    <div class="band"></div>
    <section class="medication">
      <p class="heading">Are you currently taking, or have ever taken, any of the following medication?</p>
      <div class="options"><span>Asthma inhaler<span class="check"></span></span><span>Anti-epileptics<span class="check"></span></span><span>Anti-depressants<span class="check"></span></span><span>Blood Pressure<span class="check"></span></span><span>Blood Thinners<span class="check"></span></span><span>Bisphosphonates<span class="check"></span></span></div>
      <div class="options"><span>Chemotherapy<span class="check"></span></span><span>Insulin<span class="check"></span></span><span>Immunosuppressants<span class="check"></span></span><span>Steroids<span class="check"></span></span><span>Oral Contraceptive<span class="check"></span></span><span>Other<span class="check"></span></span></div>
      <p class="heading">Please specify medication name, dose, and frequency where possible:</p>
      <div class="lines"><div class="row"><span class="field"></span></div><div class="row"><span class="field"></span></div><div class="row"><span class="field"></span></div><div class="row"><span class="field"></span></div></div>
    </section>

    <div class="band"></div>
    <section class="conditions">
      <div class="lines"><div class="row"><span class="field"></span></div></div>
      <div class="qa"><span class="q">Do you require antibiotic cover?</span>Yes<span class="check"></span>No<span class="check"></span></div>
      <div class="qa"><span class="q">Have you had a joint replacement?</span>Yes<span class="check"></span>No<span class="check"></span>Possible<span class="check"></span></div>
      <div class="qa"><span class="q">Women: &nbsp;Are you pregnant?</span>Yes<span class="check"></span>No<span class="check"></span>or &nbsp;Breast Feeding? &nbsp;Yes<span class="check"></span>No<span class="check"></span></div>
    </section>
  </div>

  <div class="turnover">Please Turnover</div>
</main>
</body>
</html>
```